Flaschenetiketten-Design in rechteckiger Grundform für Biermanufaktur
Zielgruppe
Wir repräsentieren eine Bier-Manufaktur in der Gründungsphase und sind auf der Suche nach einem Designvorschlag für die Flaschenetiketten.
Unsere Zielgruppe sind Liebhaber, die auf der Suche nach dem Speziellen und Lokalen sind. Der Biergenuss abseits des Massenmarktes soll im Entwurf sichtbar/transportiert werden. Die Bier-Manufaktur steht zeitgleich für Trend-Kreationen mit bodenständigem Ursprung.
Aufgabenstellung
Die Herkunft der Gründer Familie aus dem Schweizer Kanton Simplon soll im Vordergrund stehen, hierzu bitte das Familienwappen / einzelne Elemente siehe Dateiupload berücksichtigen.
Das Etikett soll eine rechteckige Grundform haben.
Folgende Angaben sollen sich im Etikett wiederfinden:
- Biersorte: 'Lager' (zukünftig soll es möglich sein, Biersorte auf dem Etikett zu wechseln)
Brand: 'Hearty Kandrom'
'Biermanufaktur Walliser Ursprungs'
Die Schrift soll klar und nicht zu verspielt sein.

```html
<!DOCTYPE html>
<html lang="de">
<head>
<meta charset="utf-8">
<title>Hearty Kandrom – Flaschenetiketten</title>
<link href="https://fonts.googleapis.com/css2?family=Jost:wght@500;600&display=swap" rel="stylesheet">
<style>
  :root {
    --page: #282828;
    --label: #2f2f2f;
    --label-deep: #262626;
    --ink: #ffffff;
    --ink-dark: #222222;
    --silver-light: #f2f2f2;
    --silver-mid: #a9a9a9;
    --silver-dark: #5e5e5e;
  }
  * { box-sizing: border-box; margin: 0; padding: 0; }
  html, body { width: 1200px; height: 784px; overflow: hidden; background: var(--page); }
  body { position: relative; font-family: "Jost", "Futura", sans-serif; color: var(--ink); }

  .label {
    position: absolute;
    left: 40px;
    width: 1133px;
    height: 96px;
    background: linear-gradient(180deg, var(--label) 0%, var(--label-deep) 100%);
    border: 2px solid transparent;
    border-image: linear-gradient(90deg, var(--silver-mid), var(--silver-light) 20%, var(--silver-dark) 45%, var(--silver-light) 70%, var(--silver-mid)) 1;
    box-shadow: inset 0 0 0 1px rgba(0,0,0,.5);
  }
  .label--1 { top: 117px; }
  .label--2 { top: 235px; }
  .label--3 { top: 452px; }
  .label--4 { top: 571px; }

  .crest {
    position: absolute;
    top: 4px;
    width: 68px;
    height: 84px;
    border-radius: 4px 4px 34px 34px / 4px 4px 14px 14px;
    background: linear-gradient(135deg, #e6e6e6 0%, #9a9a9a 45%, #d8d8d8 70%, #7a7a7a 100%);
    border: 1px solid var(--silver-light);
  }
  .crest--left { left: 5px; }
  .crest--right { right: 5px; }

  .brand {
    position: absolute;
    left: 95px;
    top: 4px;
    font-size: 45px;
    font-weight: 600;
    letter-spacing: 2.6px;
    line-height: 1.2;
    text-transform: uppercase;
    white-space: nowrap;
  }

  .spec, .facts {
    position: absolute;
    font-size: 16px;
    font-weight: 500;
    letter-spacing: 2px;
    line-height: 1;
    text-transform: uppercase;
    white-space: nowrap;
  }
  .spec { top: 64px; word-spacing: 4px; }
  .spec--gravity { left: 97px; }
  .spec--abv { left: 445px; width: 100px; text-align: right; letter-spacing: 1.6px; }

  .facts { left: 588px; letter-spacing: 1.7px; }
  .facts--brewed { top: 13px; width: 200px; }
  .facts--bottled { top: 13px; left: 827px; width: 220px; }
  .facts--recipe { top: 33px; }
  .facts--malt { top: 62px; }

  .date {
    position: absolute;
    top: 0;
    width: 97px;
    height: 16px;
    line-height: 16px;
  }
  .facts--brewed .date { left: 92px; }
  .facts--bottled .date { left: 111px; }
  .date--boxed {
    top: -1px;
    height: 17px;
    padding-left: 3px;
    background: var(--ink);
    color: var(--ink-dark);
    letter-spacing: 1.2px;
  }
</style>
</head>
<body>

  <section class="label label--1" aria-label="Etikett mit Angaben">
    <div class="crest crest--left" role="img" aria-label="Familienwappen in Silber"></div>
    <h1 class="brand">Hearty Kandrom</h1>
    <p class="spec spec--gravity">Stammwürze 12P</p>
    <p class="spec spec--abv">4.5Vol.%</p>
    <p class="facts facts--brewed">Gebraut:<span class="date">31.01.2019</span></p>
    <p class="facts facts--bottled">Abgefüllt:<span class="date">12.02.2019</span></p>
    <p class="facts facts--recipe">Rezept. Braukesselundkorn</p>
    <p class="facts facts--malt">Malzmischung: Pilsner, Hellmalz, Kornmalz</p>
    <div class="crest crest--right" role="img" aria-label="Familienwappen in Silber"></div>
  </section>

  <section class="label label--2" aria-label="Leeres Etikett">
    <div class="crest crest--left" role="img" aria-label="Familienwappen in Silber"></div>
    <div class="crest crest--right" role="img" aria-label="Familienwappen in Silber"></div>
  </section>

  <section class="label label--3" aria-label="Etikett mit markierten Datumsfeldern">
    <div class="crest crest--left" role="img" aria-label="Familienwappen in Silber"></div>
    <h2 class="brand">Hearty Kandrom</h2>
    <p class="spec spec--gravity">Stammwürze 12P</p>
    <p class="spec spec--abv">4.5Vol.%</p>
    <p class="facts facts--brewed">Gebraut:<span class="date date--boxed">31.01.2019</span></p>
    <p class="facts facts--bottled">Abgefüllt:<span class="date date--boxed">12.02.2019</span></p>
    <p class="facts facts--recipe">Rezept. Braukesselundkorn</p>
    <p class="facts facts--malt">Malzmischung: Pilsner, Hellmalz, Kornmalz</p>
    <div class="crest crest--right" role="img" aria-label="Familienwappen in Silber"></div>
  </section>

  <section class="label label--4" aria-label="Etikett mit leeren Datumsfeldern">
    <div class="crest crest--left" role="img" aria-label="Familienwappen in Silber"></div>
    <h2 class="brand">Hearty Kandrom</h2>
    <p class="spec spec--gravity">Stammwürze 12P</p>
    <p class="spec spec--abv">4.5Vol.%</p>
    <p class="facts facts--brewed">Gebraut:<span class="date date--boxed"></span></p>
    <p class="facts facts--bottled">Abgefüllt:<span class="date date--boxed"></span></p>
    <p class="facts facts--recipe">Rezept. Braukesselundkorn</p>
    <p class="facts facts--malt">Malzmischung: Pilsner, Hellmalz, Kornmalz</p>
    <div class="crest crest--right" role="img" aria-label="Familienwappen in Silber"></div>
  </section>

</body>
</html>
```